holloway paving service

Needs to have phone number 0418259730 and email markholloway@brightmail.com.au.
ABN 62318470915
name mark holloway

For all your concreting solutions
Excavation
Exposed & colour concrete
House & shed slabs
Driveways
Landing & steps

Contact Information for Business Card

ph 0418259730
email markholloway@brightmail.com.au.
ABN 62318470915
name mark holloway

```html
<!DOCTYPE html>
<html lang="en">
<head>
<meta charset="utf-8">
<title>Holloway Paving Service – Business Card</title>
<link rel="stylesheet" href="https://fonts.googleapis.com/css2?family=Montserrat:wght@400;500;700&display=swap">
<style>
  :root {
    --orange: #ec6a22;
    --grey: #6b6b6b;
    --grey-dark: #555555;
    --white: #ffffff;
    --stage: #e7e4df;
    --text-grey: #6f6f6f;
  }
  * { box-sizing: border-box; margin: 0; padding: 0; }
  html, body {
    width: 1200px; height: 886px; overflow: hidden;
    background: var(--stage);
    font-family: "Montserrat", sans-serif;
  }
  .stage {
    width: 1200px; height: 886px;
    display: flex; align-items: center; justify-content: center; gap: 80px;
  }
  .card {
    width: 360px; height: 580px; position: relative; overflow: hidden;
    background: var(--white);
    box-shadow: 0 10px 30px rgba(0,0,0,.18);
  }

  /* Front */
  .front__band {
    position: absolute; left: 34px; right: 34px; top: 0; bottom: 0;
    background: var(--orange);
  }
  .front__top {
    position: absolute; left: 34px; right: 34px; top: 0; height: 200px;
    background: var(--grey);
  }
  .front__brand {
    position: absolute; left: 34px; right: 34px; top: 0; height: 200px;
    display: flex; flex-direction: column; align-items: center; justify-content: center; gap: 14px;
  }
  .brand__square { width: 34px; height: 34px; background: var(--orange); }
  .front__brand .brand__name {
    color: var(--white); font-weight: 700; font-size: 17px;
    letter-spacing: 1px; text-transform: uppercase; text-align: center; line-height: 1.35;
  }
  .front__details {
    position: absolute; left: 34px; right: 34px; top: 250px;
    text-align: center; color: var(--white);
  }
  .person-name {
    font-weight: 700; font-size: 19px; letter-spacing: 1.5px; text-transform: uppercase;
    margin-bottom: 48px;
  }
  .contact-list { list-style: none; font-size: 13px; line-height: 1.9; }
  .contact-list .abn { margin-top: 16px; }

  /* Back */
  .back__brand {
    position: absolute; left: 40px; top: 70px;
    display: flex; align-items: center; gap: 12px;
  }
  .back__brand .brand__square { width: 38px; height: 38px; }
  .back__brand .brand__rule { width: 1px; height: 52px; background: var(--orange); }
  .back__brand .brand__name {
    color: var(--orange); font-weight: 700; font-size: 15px; letter-spacing: .3px;
    text-transform: uppercase; line-height: 1.15;
  }
  .back__brand .brand__phone {
    color: var(--orange); font-weight: 500; font-size: 12px; letter-spacing: 1px; margin-top: 3px;
  }
  .back__tagline {
    position: absolute; left: 0; right: 0; top: 300px;
    text-align: center; color: var(--text-grey); font-size: 12px; font-style: normal;
  }
  .services {
    position: absolute; left: 0; right: 0; top: 350px;
    list-style: none; text-align: center;
    color: var(--text-grey); font-size: 14px; line-height: 1.7;
  }
</style>
</head>
<body>
<main class="stage">
  <section class="card front" aria-label="Business card front">
    <div class="front__band"></div>
    <div class="front__top"></div>
    <div class="front__brand">
      <span class="brand__square"></span>
      <span class="brand__name">Holloway Paving<br>Service</span>
    </div>
    <div class="front__details">
      <h1 class="person-name">Mark Holloway</h1>
      <ul class="contact-list">
        <li>0418259730</li>
        <li>markholloway@brightmail.com.au</li>
        <li>www.hollowaypaving.com.au</li>
        <li class="abn">ABN 62318470915</li>
      </ul>
    </div>
  </section>

  <section class="card back" aria-label="Business card back">
    <div class="back__brand">
      <span class="brand__square"></span>
      <span class="brand__rule"></span>
      <div>
        <div class="brand__name">Holloway Paving Service</div>
        <div class="brand__phone">0418259730</div>
      </div>
    </div>
    <ul class="services">
      <li>Excavation</li>
      <li>Exposed &amp; colour concrete</li>
      <li>House &amp; shed slabs</li>
      <li>Driveways</li>
      <li>Landing &amp; steps</li>
    </ul>
  </section>
</main>
</body>
</html>
```